Spring Detox sale graphics for social media

You MUST read the Brief in the WORD document and follow the instructions there. I want to create 10 social media graphics (new Instagram size 4:5 (1080 x 1350 pixels) focusing on our Mother’s Day Spring Detox Sale graphics, using any of the pics attached. Use the attached pics, NO RANDOM STOCK PHOTOGRAPHY. For the color scheme of the graphics, they should all be complementary to the product colors or feel like Spring time.

Target Market(s)

primarily women

Requirements
Must have
• the photos and text attached

```html
<!DOCTYPE html>
<html lang="en">
<head>
<meta charset="utf-8">
<title>Spring Detox Sale – Social Graphics</title>
<link rel="stylesheet" href="https://fonts.googleapis.com/css2?family=Antonio:wght@700&family=Nunito+Sans:wght@900&display=swap">
<style>
  :root {
    --ink-bg: #000000;
    --white: #ffffff;
    --forest: #13645a;
    --emerald: #166b55;
    --orchid: #a8389b;
    --plum: #783a58;
    --wine: #63324e;
    --magenta: #d02a7c;
    --scarlet: #ff0022;
    --crimson: #cc0000;
    --indigo: #1f0a4f;
    --navy: #0d1a8a;
    --photo-a: #f1f1f3;
    --photo-b: #d9d4dc;
  }
  * { margin: 0; padding: 0; box-sizing: border-box; }
  html, body { width: 1200px; height: 2652px; overflow: hidden; background: var(--ink-bg); }
  .board { position: relative; width: 1200px; height: 2652px; }

  .card { position: absolute; width: 344px; height: 430px; overflow: hidden; background: var(--white); }
  .col-left { left: 248px; }
  .col-right { left: 607px; }
  .row-1 { top: 215px; } .row-2 { top: 663px; } .row-3 { top: 1109px; } .row-4 { top: 1557px; } .row-5 { top: 2004px; }

  .band { position: absolute; left: 0; width: 100%; }
  .line { position: absolute; left: 0; width: 100%; text-align: center; white-space: nowrap;
          font-family: "Antonio", "Arial Narrow", sans-serif; font-weight: 700; line-height: 1; text-transform: uppercase; }
  .line.start { text-align: left; padding-left: 41px; }
  .line.mixed { text-transform: none; }
  .sans { font-family: "Nunito Sans", Arial, sans-serif; font-weight: 900; text-transform: none; }

  .deal { display: inline-flex; align-items: flex-end; font-family: "Antonio", "Arial Narrow", sans-serif; font-weight: 700; line-height: 1; }
  .deal .unit { display: flex; flex-direction: column; margin-left: 4px; line-height: 0.85; }
  .deal .pct { font-size: 0.5em; }
  .deal .off { font-size: 0.36em; }
  .deal .tag { font-family: "Nunito Sans", Arial, sans-serif; font-weight: 900; font-size: 17px; text-transform: none; line-height: 1; margin: 0 0 0.9em 12px; }
  .deal.tagged .tag { margin-bottom: 36px; }

  .product-shot { position: absolute; background: linear-gradient(180deg, var(--photo-a), var(--photo-b)); border-radius: 6px; }

  .c-white { color: var(--white); }
</style>
</head>
<body>
<main class="board">

  <!-- 1 -->
  <section class="card col-left row-1">
    <div class="band" style="top:0;height:212px;background:var(--forest)"></div>
    <div class="line start c-white" style="top:40px;font-size:48px">Mother’s Day</div>
    <div class="line start c-white" style="top:87px;font-size:100px">Spring</div>
    <div class="line start mixed" style="top:232px;font-size:67px;color:var(--forest)">Detox Sale</div>
    <div class="line start" style="top:308px;color:var(--forest)">
      <span class="deal tagged" style="font-size:90px">25<span class="unit"><span class="pct">%</span><span class="off">OFF</span></span><span class="tag">Everything!</span></span>
    </div>
  </section>

  <!-- 2 -->
  <section class="card col-right row-1">
    <div class="product-shot" role="img" aria-label="Four white supplement bottles in a row" style="left:41px;top:11px;width:268px;height:113px"></div>
    <div class="line start" style="top:131px;padding-left:67px;color:var(--orchid)">
      <span class="deal" style="font-size:81px">25<span class="unit"><span class="pct">%</span><span class="off">OFF</span></span></span>
    </div>
    <div class="line start mixed" style="top:213px;padding-left:67px;font-size:45px;color:var(--orchid)">Mother’s Day</div>
    <div class="band" style="top:263px;height:167px;background:var(--orchid)"></div>
    <div class="line mixed c-white" style="top:269px;font-size:87px">Spring</div>
    <div class="line c-white" style="top:368px;font-size:46px">Detox Sale</div>
  </section>

  <!-- 3 -->
  <section class="card col-left row-2">
    <div class="band" style="top:0;height:212px;background:var(--plum)"></div>
    <div class="line c-white" style="top:35px">
      <span class="deal" style="font-size:112px">25<span class="unit"><span class="pct">%</span><span class="off">OFF</span></span></span>
    </div>
    <div class="line sans c-white" style="top:151px;font-size:31px">All Supplements</div>
    <div class="line" style="top:227px;font-size:99px;color:var(--plum)">Spring</div>
    <div class="line" style="top:328px;font-size:60px;color:var(--plum)">Detox Sale</div>
  </section>

  <!-- 4 -->
  <section class="card col-right row-2">
    <div class="line start" style="top:26px;padding-left:15px;color:var(--magenta)">
      <span class="deal" style="font-size:94px">25<span class="unit"><span class="pct">%</span><span class="off">OFF</span></span></span>
    </div>
    <div class="product-shot" role="img" aria-label="Four white supplement bottles in a row" style="left:170px;top:37px;width:162px;height:93px"></div>
    <div class="line" style="top:146px;font-size:39px;color:var(--magenta)">Spring Detox</div>
    <div class="band" style="top:196px;height:234px;background:var(--magenta)"></div>
    <div class="line c-white" style="top:214px;font-size:113px">Sale</div>
    <div class="line sans c-white" style="top:331px;font-size:28px;line-height:1.15;letter-spacing:1.5px;word-spacing:8px">Spring Reset<br>Summer Ready</div>
  </section>

  <!-- 5 -->
  <section class="card col-left row-3">
    <div class="band" style="top:0;height:213px;background:var(--scarlet)"></div>
    <div class="line start c-white" style="top:35px;padding-left:50px">
      <span class="deal tagged" style="font-size:88px">25<span class="unit"><span class="pct">%</span><span class="off">OFF</span></span><span class="tag">Everything!</span></span>
    </div>
    <div class="line c-white" style="top:134px;font-size:46px">Mother’s Day</div>
    <div class="line" style="top:241px;font-size:91px;color:var(--scarlet)">Spring</div>
    <div class="line" style="top:330px;font-size:57px;color:var(--scarlet)">Detox Sale</div>
  </section>

  <!-- 6 -->
  <section class="card col-right row-3">
    <div class="line" style="top:28px;color:var(--emerald)">
      <span class="deal" style="font-size:74px">25<span class="unit"><span class="pct">%</span><span class="off">OFF</span></span></span>
    </div>
    <div class="line" style="top:110px;font-size:37px;color:var(--emerald)">Mother’s Day</div>
    <div class="line" style="top:144px;font-size:112px;color:var(--emerald)">Sale</div>
    <div class="band" style="top:270px;height:160px;background:var(--emerald)"></div>
    <div class="line c-white" style="top:286px;font-size:39px">Feel Amazing</div>
    <div class="line c-white" style="top:325px;font-size:82px">Again!</div>
  </section>

  <!-- 7 -->
  <section class="card col-left row-4">
    <div class="band" style="top:0;height:259px;background:var(--wine)"></div>
    <div class="line c-white" style="top:28px">
      <span class="deal" style="font-size:80px">25<span class="unit"><span class="pct">%</span><span class="off">OFF</span></span></span>
    </div>
    <div class="line c-white" style="top:116px;font-size:57px">Mother’s</div>
    <div class="line c-white" style="top:174px;font-size:60px">Day Sale</div>
    <div class="line" style="top:279px;font-size:67px;color:var(--wine)">Refresh</div>
    <div class="line" style="top:350px;font-size:51px;color:var(--wine)">Your Body</div>
  </section>

  <!-- 8 -->
  <section class="card col-right row-4">
    <div class="band" style="top:0;height:277px;background:var(--crimson)"></div>
    <div class="line start c-white" style="top:26px;padding-left:185px">
      <span class="deal" style="font-size:60px">25<span class="unit"><span class="pct">%</span><span class="off">OFF</span></span></span>
    </div>
    <div class="line c-white" style="top:94px;font-size:44px;letter-spacing:-0.5px">Spring Detox</div>
    <div class="line c-white" style="top:130px;font-size:127px">Sale</div>
    <div class="line mixed" style="top:296px;font-size:48px;color:var(--crimson)">Spring Cleanse</div>
    <div class="line mixed" style="top:345px;font-size:46px;color:var(--crimson)">Summer Glow</div>
  </section>

  <!-- 9 -->
  <section class="card col-left row-5">
    <div class="band" style="top:0;height:197px;background:var(--indigo)"></div>
    <div class="line c-white" style="top:26px">
      <span class="deal" style="font-size:91px">25<span class="unit"><span class="pct">%</span><span class="off">OFF</span></span></span>
    </div>
    <div class="line c-white" style="top:130px;font-size:40px">Mother’s Day</div>
    <div class="line" style="top:217px;font-size:118px;color:var(--indigo)">Sale</div>
    <div class="line sans" style="top:340px;font-size:24px;line-height:1.15;color:var(--indigo)">Detox This Spring.<br>Shine This Summer</div>
  </section>

  <!-- 10 -->
  <section class="card col-right row-5">
    <div class="line start" style="top:30px;padding-left:34px;color:var(--navy)">
      <span class="deal" style="font-size:75px">25<span class="unit"><span class="pct">%</span><span class="off">OFF</span></span></span>
    </div>
    <div class="product-shot" role="img" aria-label="Four white supplement bottles in a row" style="left:170px;top:19px;width:164px;height:98px"></div>
    <div class="line start" style="top:123px;padding-left:34px;font-size:46px;color:var(--navy)">Mother’s Day</div>
    <div class="line start" style="top:163px;padding-left:32px;font-size:133px;color:var(--navy)">Sale</div>
    <div class="band" style="top:310px;height:120px;background:var(--navy)"></div>
    <div class="line start mixed c-white" style="top:319px;padding-left:34px;font-size:52px">Spring Detox</div>
    <div class="line start mixed c-white" style="top:383px;padding-left:34px;font-size:36px">for a Summer Body</div>
  </section>

</main>
</body>
</html>
```